Construction business card

I need a new business card, they can connect with my logo, brand.
What we do is residential house , design and build
I like: Navy blue / black
I attached our logo, brand,
and, some idea for business card.

```html
<!DOCTYPE html>
<html lang="en">
<head>
<meta charset="utf-8">
<title>Harwick Building Group – Business Card</title>
<link href="https://fonts.googleapis.com/css2?family=Lato:wght@400;700;900&display=swap" rel="stylesheet">
<style>
  :root {
    --backdrop: #2b2b2d;
    --card-blue: #0b80e9;
    --ink-white: #ffffff;
    --emboss: rgba(0, 70, 150, 0.28);
    --card-shadow: rgba(0, 0, 0, 0.55);
  }
  * { margin: 0; padding: 0; box-sizing: border-box; }
  html, body {
    width: 1200px;
    height: 992px;
    overflow: hidden;
    background: var(--backdrop);
    font-family: "Lato", sans-serif;
  }
  .canvas { position: relative; width: 1200px; height: 992px; }
  .card {
    position: absolute;
    width: 600px;
    height: 343px;
    background: var(--card-blue);
    color: var(--ink-white);
    box-shadow: 0 14px 30px var(--card-shadow);
  }
  .card--front { left: 170px; top: 110px; }
  .card--back { left: 430px; top: 520px; }

  .brand {
    position: absolute;
    left: 50%;
    top: 50%;
    transform: translate(-50%, -50%);
    display: flex;
    align-items: center;
    gap: 18px;
    white-space: nowrap;
  }
  .brand__mark {
    width: 34px;
    height: 34px;
    background: var(--ink-white);
    flex: none;
  }
  .brand__name {
    font-weight: 900;
    font-size: 30px;
    letter-spacing: 2px;
    text-transform: uppercase;
    line-height: 1.05;
  }

  .contact { position: absolute; left: 48px; top: 70px; }
  .contact__name {
    font-size: 30px;
    font-weight: 400;
    letter-spacing: 1px;
    text-transform: uppercase;
  }
  .contact__role { font-size: 15px; margin-top: 4px; margin-left: 24px; }
  .contact__address { font-size: 15px; line-height: 1.4; margin-top: 22px; margin-left: 60px; }
  .contact__list { list-style: none; margin-top: 16px; margin-left: 100px; }
  .contact__item {
    display: flex;
    align-items: center;
    gap: 12px;
    font-size: 15px;
    line-height: 1.7;
  }
  .contact__icon { width: 16px; height: 16px; flex: none; }

  .brand--faint {
    left: auto;
    right: 30px;
    top: 120px;
    transform: none;
    color: var(--emboss);
  }
  .brand--faint .brand__mark { background: var(--emboss); width: 28px; height: 28px; }
  .brand--faint .brand__name { font-size: 24px; }
</style>
</head>
<body>
<main class="canvas">
  <section class="card card--front" aria-label="Card front">
    <div class="brand">
      <span class="brand__mark"></span>
      <span class="brand__name">Harwick<br>Building Group</span>
    </div>
  </section>

  <section class="card card--back" aria-label="Card back">
    <div class="contact">
      <h1 class="contact__name">Daniel Porter</h1>
      <p class="contact__role">Owner</p>
      <p class="contact__address">42 Ferncliff Road,<br>Ashvale, Vic 3190</p>
      <ul class="contact__list">
        <li class="contact__item">
          <svg class="contact__icon" viewBox="0 0 16 16" aria-hidden="true"><path fill="#fff" d="M3.5 1.5l2.3 2.6-1.2 1.6c.8 1.9 2.2 3.3 4.1 4.2l1.6-1.2 2.7 2.3-1.2 2.3C6.9 13.2 2.7 9 2.4 2.8z"/></svg>
          <span>0400 555 018</span>
        </li>
        <li class="contact__item">
          <svg class="contact__icon" viewBox="0 0 16 16" aria-hidden="true"><rect x="1" y="3" width="14" height="10" fill="#fff"/><path d="M1 3l7 6 7-6" fill="none" stroke="#0b80e9" stroke-width="1.4"/></svg>
          <span>info@harwickbuild.com</span>
        </li>
        <li class="contact__item">
          <svg class="contact__icon" viewBox="0 0 16 16" aria-hidden="true"><circle cx="8" cy="8" r="7" fill="#fff"/><path d="M1 8h14M8 1c-3 3-3 11 0 14M8 1c3 3 3 11 0 14" fill="none" stroke="#0b80e9" stroke-width="1.1"/></svg>
          <span>www.harwickbuild.com</span>
        </li>
      </ul>
    </div>
    <div class="brand brand--faint" aria-hidden="true">
      <span class="brand__mark"></span>
      <span class="brand__name">Harwick<br>Building Group</span>
    </div>
  </section>
</main>
</body>
</html>
```